Website update for Harborline Ledger Partners & Bookkeeping

Our website needs updating
www.harborlineledgerpartners.com
Here are some of our latest print pieces to use as a guide?
I have also attached our graphic identity guide which includes the Pantone colors

Target Market(s)

Insurance Agencies

Industry/Entity Type

Accounting

Number of Pages Required

5+ page

```html
<!DOCTYPE html>
<html lang="en">
<head>
<meta charset="utf-8">
<title>Harborline Ledger Partners &amp; Bookkeeping</title>
<link href="https://fonts.googleapis.com/css2?family=Open+Sans:wght@400;600;700&family=Roboto+Condensed:wght@300;400;700&display=swap" rel="stylesheet">
<style>
:root{
  --teal:#19b1a2;
  --teal-dark:#0f8479;
  --teal-footer:#22b4a5;
  --teal-soft:#c9f4ee;
  --ink:#3d3d3d;
  --muted:#6f6f6f;
  --grey-bg:#ececec;
  --grey-dark:#6d6d6d;
  --grey-light:#cfcfcf;
  --white:#ffffff;
}
*{box-sizing:border-box;margin:0;padding:0}
html,body{width:1200px;height:2604px;overflow:hidden}
body{position:relative;background:var(--white);font-family:"Open Sans",sans-serif;color:var(--ink)}
.abs{position:absolute}

/* header + hero */
.hero{left:0;top:0;width:1200px;height:600px;background:linear-gradient(120deg,#f4f6f7 0%,#e3e8ea 40%,#c9d3d8 62%,#eef1f2 100%)}
.site-header{left:0;top:0;width:1200px;height:92px;background:rgba(255,255,255,.88)}
.brand{left:40px;top:18px;display:flex;align-items:center;gap:12px}
.brand-mark{width:44px;height:44px;background:var(--teal)}
.brand-name{font-family:"Roboto Condensed",sans-serif;font-weight:700;font-size:20px;line-height:1.1;color:var(--teal);width:230px}
.main-nav{right:40px;top:38px;display:flex;gap:34px;font-size:14px;color:var(--muted)}
.main-nav .active{color:var(--teal);font-weight:600}

/* services */
.services{left:0;top:600px;width:1200px;height:440px;background:var(--grey-bg)}
.service{width:200px;text-align:center}
.service .icon{display:block;margin:0 auto}
.service p{margin-top:12px;font-family:"Roboto Condensed",sans-serif;font-size:15px;line-height:1.25;text-transform:uppercase;color:var(--ink)}

/* intro band */
.intro-band{left:0;top:1040px;width:1200px;height:230px;background:var(--teal);display:flex;align-items:center;justify-content:center}
.intro-band h2{font-family:"Roboto Condensed",sans-serif;font-weight:400;font-size:40px;line-height:1.3;color:var(--white);text-align:center;width:960px}

.welcome{left:190px;top:1300px;width:820px;font-size:13px;line-height:1.7;color:var(--muted);text-align:center}
.btn-outline{left:540px;top:1440px;width:120px;height:30px;border:2px solid var(--teal);border-radius:15px;color:var(--teal);font-size:11px;font-weight:600;text-transform:uppercase;display:flex;align-items:center;justify-content:center}

/* costs */
.section-title{font-family:"Roboto Condensed",sans-serif;font-weight:400;font-size:48px;color:var(--ink);text-align:center;width:1200px;left:0}
.cost-title{top:1500px}
.cost-circle{width:200px;height:200px;border-radius:50%;display:flex;align-items:center;justify-content:center;text-align:center;font-family:"Roboto Condensed",sans-serif;font-size:26px;line-height:1.2}
.cost-circle.revenue{left:260px;top:1690px;background:var(--grey-dark);color:var(--white)}
.cost-circle.fee{left:740px;top:1690px;background:var(--grey-light);color:var(--grey-dark)}
.range{left:500px;width:200px;height:44px;border:1px solid #d6d6d6;background:#fafafa;font-size:13px;color:var(--muted);display:flex;align-items:center;justify-content:center}

/* testimonials */
.testimonials{left:0;top:1960px;width:1200px;height:320px;background:var(--teal-soft)}
.testimonials .section-title{top:18px;color:var(--teal-dark)}
.client-photo{left:150px;top:2080px;width:120px;height:120px;border-radius:50%;background:radial-gradient(circle at 50% 40%,#e8d4c4,#9a8a80);border:4px solid var(--white)}
.quote{left:320px;top:2100px;width:720px;font-size:14px;line-height:1.6;color:var(--muted);font-style:italic}
.client-name{left:320px;top:2180px;font-size:15px;font-weight:600;color:var(--teal)}
.dots{left:560px;top:2245px;display:flex;gap:10px}
.dots span{width:10px;height:10px;border-radius:50%;background:var(--white)}
.dots .on{background:var(--teal)}

/* footer */
.site-footer{left:0;top:2280px;width:1200px;height:274px;background:var(--teal-footer);color:var(--white)}
.footer-col{top:2305px;width:240px}
.footer-col h4{font-family:"Roboto Condensed",sans-serif;font-weight:400;font-size:20px;margin-bottom:14px}
.footer-col li{list-style:none;font-size:12px;line-height:2;opacity:.9}
.footer-col p{font-size:12px;line-height:1.7;opacity:.9}
.signup{margin-top:14px;display:flex}
.signup span{height:30px;background:var(--white);flex:1}
.signup b{width:34px;height:30px;background:var(--teal-dark)}
.post{display:flex;gap:8px;margin-bottom:10px}
.post i{flex:none;width:8px;height:8px;background:var(--white);margin-top:6px}
.contact-row{display:flex;align-items:center;gap:10px;margin-bottom:12px;font-size:12px}
.bottom-bar{left:0;top:2554px;width:1200px;height:50px;background:var(--teal-dark);color:var(--white);font-size:12px}
.bottom-bar .copy{left:40px;top:17px}
.social{right:60px;top:15px;display:flex;gap:14px}
.social span{width:20px;height:20px;border-radius:50%;background:rgba(255,255,255,.85)}
</style>
</head>
<body>

<div class="abs hero" role="img" aria-label="Photo of three business colleagues smiling around a laptop in a bright office"></div>

<header class="abs site-header">
  <div class="abs brand">
    <span class="brand-mark"></span>
    <span class="brand-name">Harborline Ledger Partners &amp; Bookkeeping</span>
  </div>
  <nav class="abs main-nav">
    <span class="active">Home</span><span>About Us</span><span>Company</span><span>Our Services</span><span>How it Works</span><span>Resources</span><span>Contact Us</span><span>Blog</span>
  </nav>
</header>

<section class="abs services">
  <svg width="0" height="0" style="position:absolute">
    <defs>
      <g id="ring"><circle cx="50" cy="50" r="48" fill="#fff" stroke="#9a9a9a" stroke-width="3"/><circle cx="50" cy="50" r="38" fill="#e4e4e4"/></g>
    </defs>
  </svg>

  <div class="abs service" style="left:108px;top:70px">
    <svg class="icon" width="100" height="100"><circle cx="50" cy="50" r="48" fill="#fff" stroke="var(--teal)" stroke-width="3"/><circle cx="50" cy="50" r="38" fill="var(--teal-soft)"/><rect x="34" y="36" width="32" height="26" fill="var(--teal)"/><rect x="30" y="62" width="40" height="6" fill="var(--teal-dark)"/></svg>
    <p style="color:var(--teal-dark)">Record Direct Bill<br>Commission</p>
  </div>
  <div class="abs service" style="left:388px;top:70px">
    <svg class="icon" width="100" height="100"><use href="#ring"/><circle cx="50" cy="50" r="16" fill="#9a9a9a"/><path d="M43 50h14M50 43v14" stroke="#fff" stroke-width="3"/></svg>
    <p>Reconcile &amp; PM Agency Bill<br>Premiums</p>
  </div>
  <div class="abs service" style="left:628px;top:70px">
    <svg class="icon" width="100" height="100"><use href="#ring"/><rect x="36" y="32" width="28" height="36" fill="#9a9a9a"/><path d="M41 42h18M41 50h18M41 58h12" stroke="#fff" stroke-width="2"/></svg>
    <p>Reconcile General Ledger<br>Accounts</p>
  </div>
  <div class="abs service" style="left:900px;top:70px">
    <svg class="icon" width="100" height="100"><use href="#ring"/><rect x="32" y="36" width="36" height="24" fill="#9a9a9a"/><rect x="28" y="60" width="44" height="5" fill="#7a7a7a"/></svg>
    <p>Prepare &amp; Internet Financial<br>Statements</p>
  </div>

  <div class="abs service" style="left:260px;top:250px">
    <svg class="icon" width="100" height="100"><use href="#ring"/><path d="M36 40h28v22H36z" fill="#9a9a9a"/><path d="M36 40l14 12 14-12" stroke="#fff" stroke-width="2" fill="none"/></svg>
    <p>PM Vendor Invoices</p>
  </div>
  <div class="abs service" style="left:508px;top:250px">
    <svg class="icon" width="100" height="100"><use href="#ring"/><rect x="30" y="40" width="40" height="20" fill="none" stroke="#c0392b" stroke-width="3"/><path d="M36 50h28" stroke="#c0392b" stroke-width="3"/></svg>
    <p>Reconcile Customer<br>Accounts Receivable</p>
  </div>
  <div class="abs service" style="left:760px;top:250px">
    <svg class="icon" width="100" height="100"><use href="#ring"/><circle cx="50" cy="50" r="18" fill="none" stroke="#9a9a9a" stroke-width="4"/><path d="M50 40v10l7 5" stroke="#9a9a9a" stroke-width="3" fill="none"/></svg>
    <p>Process Payroll</p>
  </div>
</section>

<section class="abs intro-band">
  <h2>HLPB is a professional Accounting/Bookkeeping firm located in Connecticut dedicated exclusively to Independent Insurance Agencies.</h2>
</section>

<p class="abs welcome">Welcome to HLPB. After working in-house at agencies for many years, Nora Whitfield formed HLPB in 2011 to help Independent Insurance Agencies manage their accounting and bookkeeping. HLPB currently has 12 staff members working in our Connecticut office, trained in all aspects of agency accounting. We have just added the capacity for new clients and additional staff members. Call us, we'll be ready to make your process simple.</p>
<div class="abs btn-outline">Learn More</div>

<h2 class="abs section-title cost-title">What It Costs</h2>
<svg class="abs" style="left:0;top:1580px" width="1200" height="120">
  <path d="M600 0v40M360 40h480M360 40v70M840 40v70M600 40v20" stroke="#bdbdbd" stroke-width="2" fill="none"/>
</svg>
<div class="abs cost-circle revenue">Annual<br>Commission<br>Revenue</div>
<div class="abs cost-circle fee">Average<br>Monthly<br>Service Fee</div>
<div class="abs range" style="top:1640px">+ $3,000,000</div>
<div class="abs range" style="top:1694px">$2,000,000 &ndash; $3,000,000</div>
<div class="abs range" style="top:1748px">$1,000,000 &ndash; $2,000,000</div>
<div class="abs range" style="top:1802px">$500,000 &ndash; $1,000,000</div>

<section class="abs testimonials">
  <h2 class="abs section-title">What Our Clients Say</h2>
  <svg class="abs" style="left:30px;top:150px" width="1140" height="40">
    <path d="M14 4L2 20l12 16" stroke="#9fd9d1" stroke-width="4" fill="none"/>
    <path d="M1126 4l12 16-12 16" stroke="#9fd9d1" stroke-width="4" fill="none"/>
  </svg>
</section>
<div class="abs client-photo" role="img" aria-label="Portrait photo of a satisfied client"></div>
<p class="abs quote">"Working with this team has changed how our agency runs. Our books are always current, commissions reconcile each month, and we finally have clear financial statements we trust to plan growth and serve our clients well."</p>
<div class="abs client-name">Martin Hale</div>
<div class="abs dots"><span class="on"></span><span></span><span></span><span></span><span></span></div>

<footer class="abs site-footer"></footer>
<div class="abs footer-col" style="left:60px">
  <h4>Navigate</h4>
  <ul><li>Terms &amp; Conditions</li><li>Disclaimer</li><li>Privacy Policy</li><li>Careers</li><li>Sitemap</li></ul>
</div>
<div class="abs footer-col" style="left:340px">
  <h4>Newsletter</h4>
  <p>Sign up for our monthly newsletter to receive agency accounting tips, updates and news straight to your inbox.</p>
  <div class="signup"><span></span><b></b></div>
</div>
<div class="abs footer-col" style="left:620px">
  <h4>Recent Posts</h4>
  <div class="post"><i></i><p>Closing the month faster with clean commission records</p></div>
  <div class="post"><i></i><p>Five ledger checks every agency should run quarterly</p></div>
  <div class="post"><i></i><p>Payroll deadlines to watch this coming season</p></div>
</div>
<div class="abs footer-col" style="left:900px">
  <h4>Contact Info</h4>
  <div class="contact-row"><svg width="16" height="18"><path d="M8 1a6 6 0 0 1 6 6c0 5-6 10-6 10S2 12 2 7a6 6 0 0 1 6-6z" fill="#fff"/><circle cx="8" cy="7" r="2" fill="var(--teal-footer)"/></svg><span>HLPB &middot; 214 Quarry Road<br>Milford, CT 06460</span></div>
  <div class="contact-row"><svg width="16" height="16"><path d="M3 1l3 0 2 4-2 2a9 9 0 0 0 4 4l2-2 4 2v3a2 2 0 0 1-2 2A13 13 0 0 1 1 3a2 2 0 0 1 2-2z" fill="#fff"/></svg><span>(203) 555-0148</span></div>
  <div class="contact-row"><svg width="16" height="12"><rect width="16" height="12" fill="#fff"/><path d="M0 0l8 7 8-7" stroke="var(--teal-footer)" stroke-width="1.5" fill="none"/></svg><span>hello@harborlineledgerpartners.com</span></div>
</div>

<div class="abs bottom-bar">
  <span class="abs copy">&copy; Harborline Ledger Partners &amp; Bookkeeping 2015. All rights reserved. &middot; www.harborlineledgerpartners.com</span>
  <div class="abs social"><span></span><span></span><span></span><span></span></div>
</div>

</body>
</html>
```